Modern & Aesthetic Electrician Sign Design for Work Vehicle

Modern and aesthetic signage design for an electricians work vehicle. Including already designed logo, mobile number, ABN, licensing number and services offered. Preference is black background, symmetric design with logo centred, services offered at bottom of sign in smaller size font. Mobile number readable and big enough to standout without being too large.

Industry/Entity Type

Electrician

Font styles to use
Serif
Sans Serif

Colors
000000
ffffff
ec1f27

Requirements
Must have
• Logo
• Services Offered
• Mobile Number
• ABN
• License Number
• Black background

```html
<!DOCTYPE html>
<html lang="en">
<head>
<meta charset="utf-8">
<title>Halls Electrical – Vehicle Sign</title>
<link rel="stylesheet" href="https://fonts.googleapis.com/css2?family=Michroma&family=Montserrat:wght@500&display=swap">
<style>
  :root {
    --black: #000000;
    --white: #ffffff;
    --red: #ec1f27;
    --charcoal: #353535;
    --frame: #111111;
    --caption: #555555;
  }
  html, body {
    margin: 0;
    padding: 0;
    overflow: hidden;
    background: var(--white);
  }
  .canvas {
    position: relative;
    width: 1200px;
    height: 1000px;
    background: var(--white);
    overflow: hidden;
  }
  .frame-line {
    position: absolute;
    background: var(--frame);
  }
  .frame-top    { left: 105px;  top: 35px;  width: 1060px; height: 3px; }
  .frame-right  { left: 1162px; top: 35px;  width: 3px;    height: 900px; }
  .frame-left   { left: 40px;   top: 105px; width: 3px;    height: 854px; }
  .frame-bottom { left: 40px;   top: 956px; width: 942px;  height: 3px; }

  .sign {
    position: absolute;
    left: 193px;
    top: 179px;
    width: 856px;
    height: 499px;
    background: var(--black);
    overflow: hidden;
    box-shadow: 0 30px 50px rgba(0,0,0,0.18);
    font-family: "Michroma", sans-serif;
    color: var(--white);
  }
  .credentials {
    position: absolute;
    right: 14px;
    top: 16px;
    text-align: right;
    font-size: 10.5px;
    letter-spacing: 1.6px;
    line-height: 17px;
  }
  .brand {
    position: absolute;
    left: 0;
    right: 0;
    top: 40px;
    text-align: center;
  }
  .brand-ring {
    display: block;
    margin: 0 auto;
    width: 170px;
    height: 170px;
    border: 7px solid var(--white);
    border-radius: 50%;
    box-sizing: border-box;
  }
  .brand-name {
    margin-top: 18px;
    font-size: 28px;
    letter-spacing: 3px;
    color: var(--red);
    line-height: 1;
  }
  .services {
    position: absolute;
    left: 0;
    right: 0;
    top: 347px;
    text-align: center;
    font-size: 11.5px;
    letter-spacing: 2.1px;
    line-height: 18px;
  }
  .services .dot {
    display: inline-block;
    width: 6px;
    height: 6px;
    border-radius: 50%;
    background: var(--red);
    margin: 0 8px;
    vertical-align: middle;
  }
  .contact-band {
    position: absolute;
    left: 0;
    bottom: 0;
    width: 856px;
    height: 74px;
  }
  .phone {
    position: absolute;
    left: 187px;
    top: 447px;
    display: flex;
    align-items: center;
    gap: 14px;
    font-size: 34px;
    letter-spacing: 5px;
    color: var(--white);
  }
  .phone-icon {
    width: 36px;
    height: 36px;
  }
  .size-caption {
    position: absolute;
    left: 193px;
    top: 718px;
    font-family: "Montserrat", sans-serif;
    font-weight: 500;
    font-size: 13px;
    letter-spacing: 3.5px;
    color: var(--caption);
  }
</style>
</head>
<body>
<div class="canvas">
  <div class="frame-line frame-top"></div>
  <div class="frame-line frame-right"></div>
  <div class="frame-line frame-left"></div>
  <div class="frame-line frame-bottom"></div>

  <section class="sign">
    <div class="credentials">
      <div>ABN 12 345 678 901</div>
      <div>LICENCE NO. 100234A</div>
    </div>

    <div class="brand">
      <span class="brand-ring"></span>
      <div class="brand-name">HALLS ELECTRICAL</div>
    </div>

    <div class="services">
      <div>LIGHTING &amp; POWER<span class="dot"></span>DATA &amp; COMMUNICATIONS<span class="dot"></span>AUDIO VISUAL &amp; TV<span class="dot"></span>SECURITY</div>
      <div>AUTOMATION<span class="dot"></span>EMERGENCY CALL OUT SERVICES<span class="dot"></span>SWITCHBOARD UPGRADES</div>
    </div>

    <svg class="contact-band" viewBox="0 0 856 74" preserveAspectRatio="none">
      <polygon points="712,0 856,0 856,74 812,74 788,36" fill="var(--charcoal)"/>
      <polygon points="788,36 856,14 856,74 812,74" fill="var(--white)"/>
      <polygon points="0,0 712,0 747,52 640,74 0,74" fill="var(--red)"/>
    </svg>

    <div class="phone">
      <svg class="phone-icon" viewBox="0 0 36 36">
        <circle cx="18" cy="18" r="18" fill="var(--white)"/>
        <path d="M12.5 9.5c1-.6 2-.3 2.5.6l1.6 3c.4.8.2 1.7-.5 2.2l-1.1.8c.8 2 2.4 3.7 4.4 4.6l.9-1.1c.5-.7 1.4-.9 2.2-.5l3 1.6c.9.5 1.2 1.6.6 2.5l-1 1.5c-.8 1.1-2.2 1.6-3.5 1.2-5.2-1.7-9.2-5.8-10.8-11-.4-1.3.1-2.7 1.2-3.5z" fill="var(--red)"/>
      </svg>
      <span>0400 123 456</span>
    </div>
  </section>

  <div class="size-caption">1200 x 700 mm</div>
</div>
</body>
</html>
```